Harrowgate Patrol Service Business Card Design

Hi All

We have decided to update this project from the Brightmoor Protective and Patrol Outfitters to the one mentioned above.

We are a company that supplies guard services .
Updates

Project Deadline Extended
Reason: Since we have changed the projet to a new design and idea this gives veryone more time. we are all busy regards greg

please include the following details on the card

 Master License 527194638 or M/L 527194638

phone 02 7316 2948

the logo can be removed from the shield , ie scales and eagle with the writing    etc

thank you                       

Hi All

There are great design that have come in so far and thank you for your time and design.

Please adjust the design to include

Company Name

Name  - Gregory Talbot

Address - PO Box 358 Redfern 2016

Master License Number - 527 194 638

ABN - 73204 518962 

Web address  www.harrowgatepatrolservice.com.au

email -  security@harrowgatepatrolservice.com.au

Thank you

Greg

                                   

Target Market(s)

Commercial, Residential, Business, Government, Corporate

Industry/Entity Type

Business

Contact Information for Business Card

Gregory Talbot
General Manager 0438 271 594
ABN 73 204 518 962 0273162948
PO Box 358
Redfern 2016

www.harrowgatepatrolservice.com.au

Requirements
Must have
• the company logo as per attachment below

```html
<!DOCTYPE html>
<html lang="en">
<head>
<meta charset="utf-8">
<title>Harrowgate Patrol Service – Business Card</title>
<link rel="stylesheet" href="https://fonts.googleapis.com/css2?family=Electrolize&family=Michroma&display=swap">
<style>
  :root {
    --page-bg: #23262b;
    --brand-blue: #00aeef;
    --band-light: #ffffff;
    --band-mid: #e4e6e8;
    --band-edge: #c9ccd0;
    --ink-white: #ffffff;
    --ink-grey: #6d7075;
  }
  * { box-sizing: border-box; margin: 0; padding: 0; }
  html, body {
    width: 1200px;
    height: 860px;
    overflow: hidden;
    background: var(--page-bg);
  }
  body {
    display: flex;
    align-items: center;
    justify-content: center;
  }
  .business-card {
    width: 1000px;
    height: 570px;
    display: flex;
    box-shadow: 0 18px 40px rgba(0,0,0,0.45);
  }
  .contact-panel {
    width: 620px;
    height: 100%;
    background: var(--brand-blue);
    color: var(--ink-white);
    padding: 56px 0 0 56px;
    font-family: "Electrolize", sans-serif;
  }
  .holder-name {
    font-size: 26px;
    font-weight: 400;
    letter-spacing: 1px;
    text-transform: uppercase;
    margin-bottom: 40px;
  }
  .holder-role {
    font-size: 17px;
    letter-spacing: 1px;
    margin: -32px 0 30px;
  }
  .postal-address {
    font-size: 19px;
    line-height: 1.45;
    font-style: normal;
    margin-bottom: 26px;
  }
  .contact-list {
    list-style: none;
    font-size: 17px;
    line-height: 1.95;
    letter-spacing: 1px;
  }
  .company-band {
    width: 170px;
    height: 100%;
    background: radial-gradient(ellipse at 50% 50%, var(--band-light) 0%, var(--band-mid) 70%, var(--band-edge) 100%);
    display: flex;
    align-items: center;
    justify-content: center;
  }
  .company-name {
    writing-mode: vertical-rl;
    transform: rotate(180deg);
    display: flex;
    flex-direction: column;
    align-items: flex-start;
  }
  .company-primary {
    font-family: "Michroma", sans-serif;
    color: var(--brand-blue);
    font-size: 22px;
    letter-spacing: 3px;
    text-transform: uppercase;
  }
  .company-secondary {
    font-family: "Michroma", sans-serif;
    color: var(--ink-grey);
    font-size: 13px;
    letter-spacing: 2px;
    text-transform: uppercase;
    margin-left: 6px;
  }
  .social-band {
    flex: 1;
    height: 100%;
    background: var(--brand-blue);
    display: flex;
    align-items: flex-end;
    justify-content: center;
    gap: 18px;
    padding-bottom: 48px;
  }
  .social-link {
    writing-mode: vertical-rl;
    transform: rotate(180deg);
    display: flex;
    align-items: center;
    gap: 14px;
    font-family: "Electrolize", sans-serif;
    color: var(--ink-white);
    font-size: 30px;
    letter-spacing: 1px;
  }
  .social-marker {
    width: 30px;
    height: 30px;
    background: var(--ink-white);
    border-radius: 3px;
  }
</style>
</head>
<body>
  <main class="business-card">
    <section class="contact-panel">
      <h1 class="holder-name">Gregory Talbot</h1>
      <p class="holder-role">General Manager</p>
      <address class="postal-address">PO Box 358<br>Redfern 2016</address>
      <ul class="contact-list">
        <li>Phone 02 7316 2948</li>
        <li>Mobile 0438 271 594</li>
        <li>M/L 527 194 638</li>
        <li>ABN 73 204 518 962</li>
        <li>security@harrowgatepatrolservice.com.au</li>
        <li>www.harrowgatepatrolservice.com.au</li>
      </ul>
    </section>
    <section class="company-band">
      <div class="company-name">
        <span class="company-primary">Harrowgate</span>
        <span class="company-secondary">Patrol Service</span>
      </div>
    </section>
    <section class="social-band">
      <div class="social-link"><span class="social-marker"></span>chirpline.net/harrowgate</div>
      <div class="social-link"><span class="social-marker"></span>linkpage.net/harrowgate</div>
    </section>
  </main>
</body>
</html>
```